Design Website to Recruit next Generation of Steel Harbor's Order Vantage

Design a cool website that provides just enough information to be intriguing to teenagers who compete in combat sports. The format is to make this an invite-only team of high-school-aged competitors in combat sports (predominately Jiu Jitsu right now). Cinder Ravens can participate in similar assignments to earn consideration. We are modeled after the Order Vantage formed in Steel Harbor and would like to keep that look and feel. The document attached "OV - Ideas and Content for Website" shows our initial thoughts and here is more about us:

Goal - To promote the success of committed teenage Jiu Jitsu competitors who excel through focused preparation and deliberate practice.

Why - Prove the core principles of success.

How - Success is its own reward and always entails an element of the unknown/uncontrollable. We reward preparation. Setting clear goals (SMART), deliberate practice, building mental models (domain specific knowledge), restorative recovery, nutritional coaching, power of teaching others, sports science (strength & conditioning), expert guidance, personalized development plans, accountability, Quantified Self, gamification and competitive challenges. What - We will win at the highest of levels across the fight world by applying the general principles of success. These lessons will be carried with them to other areas of their lives.

Our primary goal with the website would be to share our company’s mission statement and promote the success of our sponsored athletes.

The only social media account we have currently is Pixtrelle's @ordervantageK7 (recently established). If you want more of an idea for what our online presence should feel like, then I would suggest watching these two scenes from Steel Harbor:

Recruiting: This scene shows the process for joining Order Vantage: https://vidrelo.net/Qk82LmTrA

Order Vantage Assignments: This shows how assignments are handed out for members to accomplish: https://vidrelo.net/Zp41XwNeB

Order Vantage Color Assignment: This is their first large assignment and where the green color comes from: https://vidrelo.net/Hd67VcJuC

It is also worth noting that "less is more" considering the first rule is, "you do not talk about..." That should carry over to our website and social media presence. We want to share just enough to be intriguing to inquiring minds and motivational for members, but no more.

I have uploaded a bunch of content, but just wanted to give you a broader idea. Feel free to design as you see fit...
Updates

Please stay tuned for the "burning smiley face" files. I have purchased a rendering of it so we have a proprietary vector image to use on our site. There will also be files for different versions of the Order Vantage//OV logos for various subcategories. Here is how they are to be applied: Circled = Primary (for main/landing page), Jiu Jitsu = Pyramid, Wrestling = Traditional, Muay Thai = Rolled, and Legacy OV = Original (coming soon).

Target Market(s)

Teenage competitors of combat sports, their parents, and sponsors of those athletes

Industry/Entity Type

Martial Arts & High School Sports

Coding

Coded - Design and coding required

Number of Pages Required

5+ page

Font styles to use
Sans Serif
Other font styles liked:
• See font in "Circled Logo"

Colors
59FF00
82FF00
B8FF75
E3FFCB
F4FFEA
EB3D1F
EC4F4E
F09395
F8D3D4
FCEDEE

Requirements
Must have
• Cool landing page with logo and brief summary of what we do. Page with 8 rules and explanation for earning an invitation. Plus, accomplishments page for memorializing the success of sponsored "Cinder Ravens"
Should not have
• Individual names

```html
<!DOCTYPE html>
<html lang="en">
<head>
<meta charset="utf-8">
<title>Order Vantage</title>
<link rel="stylesheet" href="https://fonts.googleapis.com/css2?family=Kanit:ital,wght@0,600;0,700;0,800;1,600;1,700;1,800&family=Lato:wght@400;700&display=swap">
<style>
  :root {
    --red: #8f2519;
    --red-bright: #a8301f;
    --green: #43914a;
    --green-text: #4caf50;
    --dark: #333333;
    --ink: #111111;
    --grey-bg: #f2f2f2;
    --white: #ffffff;
    --black: #000000;
  }
  * { margin: 0; padding: 0; box-sizing: border-box; }
  html, body { width: 1200px; height: 3668px; overflow: hidden; }
  body { position: relative; background: var(--white); font-family: "Lato", sans-serif; color: var(--ink); }
  .abs { position: absolute; }
  .heading { font-family: "Kanit", sans-serif; font-weight: 700; text-transform: uppercase; }

  /* Hero */
  .hero { left: 0; top: 0; width: 1200px; height: 625px;
    background: radial-gradient(ellipse at 50% 10%, #6f7f9c 0%, #3a4560 35%, #1f2537 70%, #2c3447 100%); }
  .hero-floor { left: 0; top: 540px; width: 1200px; height: 85px;
    background: linear-gradient(180deg, #56627a 0%, #8a95aa 60%, #a7b0c2 100%); }
  .brand-top { left: 118px; top: 50px; color: var(--green-text); font-family: "Kanit", sans-serif; font-weight: 700; font-size: 22px; line-height: 36px; }
  .menu { left: 1015px; top: 56px; color: var(--white); font-family: "Kanit", sans-serif; font-weight: 700; font-size: 16px; letter-spacing: .5px; display: flex; align-items: center; gap: 6px; }
  .hero-title { left: 0; top: 168px; width: 1200px; text-align: center; color: var(--white); font-size: 70px; line-height: 82px; font-weight: 800; font-style: italic; }
  .btn { display: flex; align-items: center; justify-content: center; background: var(--red-bright); color: var(--white); font-family: "Kanit", sans-serif; font-weight: 700; text-transform: uppercase; border-radius: 4px; }
  .hero-btn { left: 518px; top: 359px; width: 164px; height: 55px; font-size: 17px; }

  /* Army section */
  .army { left: 0; top: 625px; width: 1200px; height: 467px; background: var(--dark); overflow: hidden; }
  .army-blob { left: -60px; top: -40px; width: 820px; height: 420px; border-radius: 0 0 60% 40%; background: #3b3b3b; }
  .army-title { left: 112px; top: 705px; color: var(--white); font-size: 34px; line-height: 48px; font-style: italic; }
  .army-sub { left: 112px; top: 762px; color: var(--red-bright); font-family: "Kanit", sans-serif; font-weight: 600; font-size: 18px; text-transform: uppercase; }
  .army-text { left: 112px; top: 815px; width: 455px; color: #e6e6e6; font-size: 17px; line-height: 28px; }
  .army-trust { left: 112px; top: 942px; color: var(--green-text); font-family: "Kanit", sans-serif; font-weight: 700; font-size: 17px; text-transform: uppercase; }
  .army-portrait { left: 731px; top: 659px; width: 328px; height: 328px; border-radius: 50%;
    background: radial-gradient(circle at 50% 40%, #2f6b5c 0%, #1c3b35 60%, #141414 100%); }

  /* Preparation wheel */
  .prep-title { left: 0; top: 1168px; width: 1200px; text-align: center; font-size: 34px; line-height: 51px; font-style: italic; font-weight: 800; }
  .side-note { font-family: "Kanit", sans-serif; font-style: italic; font-weight: 700; font-size: 16px; line-height: 30px; text-transform: uppercase; }
  .note-left { left: 88px; top: 1369px; }
  .note-right { left: 834px; top: 1388px; }
  .wheel { left: 321px; top: 1314px; width: 560px; height: 560px; }
  .wheel text { font-family: "Kanit", sans-serif; font-weight: 700; text-transform: uppercase; }
  .prep-quote { left: 0; top: 1911px; width: 1200px; text-align: center; font-family: "Kanit", sans-serif; font-style: italic; font-weight: 700; font-size: 19px; line-height: 31px; text-transform: uppercase; }

  /* Rules */
  .rules { left: 0; top: 2056px; width: 1200px; height: 751px; background: var(--grey-bg); }
  .rules-photo { left: 68px; top: 2148px; width: 368px; height: 518px;
    background: linear-gradient(160deg, #6b4a2e 0%, #a37a52 45%, #d9c5a8 75%, #8a6a4a 100%); }
  .rules-title { left: 476px; top: 2140px; font-size: 34px; line-height: 51px; font-style: italic; font-weight: 800; }
  .rule-list { left: 478px; top: 2267px; list-style: none; }
  .rule { display: flex; align-items: center; height: 58.4px; }
  .rule-badge { width: 42px; height: 42px; border-radius: 50%; border: 2px solid var(--red); background: var(--red);
    box-shadow: inset 0 0 0 2px var(--white); color: var(--white); display: flex; flex-direction: column; align-items: center; justify-content: center; font-family: "Kanit", sans-serif; font-weight: 700; line-height: 1; }
  .rule-num { font-size: 16px; }
  .rule-tag { font-size: 7px; }
  .rule-text { margin-left: 17px; font-family: "Kanit", sans-serif; font-weight: 600; font-size: 15px; text-transform: uppercase; }

  /* Footer */
  .footer { left: 0; top: 3116px; width: 1200px; height: 552px; background: var(--black); }
  .faq { left: 120px; top: 2885px; width: 960px; height: 309px; background: var(--green); border-radius: 22px; text-align: center; color: var(--white); }
  .faq-title { margin-top: 38px; font-size: 36px; line-height: 44px; font-weight: 700; }
  .faq-text { margin: 22px auto 0; width: 830px; font-size: 15px; line-height: 30px; }
  .faq-btn { left: 415px; top: 232px; width: 128px; height: 42px; font-size: 13px; }
  .brand-foot { left: 0; top: 3320px; width: 1200px; text-align: center; color: var(--green-text); font-family: "Kanit", sans-serif; font-weight: 700; font-size: 34px; line-height: 50px; }
  .foot-links { left: 0; top: 3450px; width: 1200px; display: flex; justify-content: center; gap: 44px; color: var(--white); font-size: 15px; }
  .copyright { left: 0; top: 3508px; width: 1200px; text-align: center; color: var(--white); font-size: 13px; }
  .copyright .link { color: var(--green-text); text-decoration: underline; }
  .socials { left: 501px; top: 3561px; display: flex; gap: 10px; }
  .social { width: 42px; height: 42px; border-radius: 50%; background: var(--white); }
  .social.is-active { background: var(--red-bright); }
</style>
</head>
<body>

<div class="abs hero" role="img" aria-label="Photo of an empty combat sports arena under bright lights"></div>
<div class="abs hero-floor" role="img" aria-label="Arena floor"></div>
<div class="abs brand-top">Order Vantage</div>
<div class="abs menu">MENU
  <svg width="14" height="12" viewBox="0 0 14 12"><rect y="0" width="14" height="2" fill="#fff"/><rect y="5" width="14" height="2" fill="#fff"/><rect y="10" width="14" height="2" fill="#fff"/></svg>
</div>
<h1 class="abs heading hero-title">Welcome to<br>Order Vantage</h1>
<div class="abs btn hero-btn">Get Started</div>

<section class="abs army">
  <div class="abs army-blob"></div>
</section>
<h2 class="abs heading army-title">Rowan built himself an army</h2>
<p class="abs army-sub">Why was Rowan building an army?</p>
<p class="abs army-text">To introduce and apply the core principles of success to highschool aged Jia Jitsa competitors.<br>We strive to work smarter not just si they can achieve their tell potherid</p>
<p class="abs army-trust">In Rowan we trust</p>
<div class="abs army-portrait" role="img" aria-label="Circular illustration of the team founder"></div>

<h2 class="abs heading prep-title">Success is it's own reward so we<br>celebrate preparation</h2>
<p class="abs side-note note-left">Without pain<br>Without sacrifice<br>We would have nothing</p>
<p class="abs side-note note-right">Success is it's own reward so<br>we celebrate preparation</p>
<svg class="abs" style="left:288px;top:1492px" width="48" height="36" viewBox="0 0 48 36"><path d="M44 30 C30 30 16 22 8 6" fill="none" stroke="#111" stroke-width="2"/><path d="M3 2 L9 14 L14 5 Z" fill="#111"/></svg>
<svg class="abs" style="left:872px;top:1480px" width="48" height="36" viewBox="0 0 48 36"><path d="M4 32 C18 32 32 24 40 8" fill="none" stroke="#111" stroke-width="2"/><path d="M45 3 L34 9 L43 15 Z" fill="#111"/></svg>

<svg class="abs wheel" viewBox="0 0 560 560" role="img" aria-label="Wheel of preparation: spirit, technical mind and body">
  <defs>
    <path id="ring-top" d="M61,360 A233,233 0 1,1 499,360"/>
    <path id="ring-bottom" d="M78,396 A233,233 0 0,0 482,396"/>
  </defs>
  <circle cx="280" cy="280" r="262" fill="var(--green)"/>
  <circle cx="280" cy="280" r="204" fill="var(--red)" stroke="#fff" stroke-width="2"/>
  <g stroke="#fff" stroke-width="2" transform="translate(280 280)">
    <line x1="0" y1="-83" x2="0" y2="-204" transform="rotate(2.5)"/>
    <line x1="0" y1="-83" x2="0" y2="-204" transform="rotate(36)"/>
    <line x1="0" y1="-83" x2="0" y2="-204" transform="rotate(67)"/>
    <line x1="0" y1="-83" x2="0" y2="-204" transform="rotate(102)"/>
    <line x1="0" y1="-83" x2="0" y2="-204" transform="rotate(140)"/>
    <line x1="0" y1="-83" x2="0" y2="-204" transform="rotate(175)"/>
    <line x1="0" y1="-83" x2="0" y2="-204" transform="rotate(218)"/>
    <line x1="0" y1="-83" x2="0" y2="-204" transform="rotate(272)"/>
    <line x1="0" y1="-83" x2="0" y2="-204" transform="rotate(322)"/>
  </g>
  <g fill="#fff" font-size="13" text-anchor="middle" transform="translate(280 280)">
    <g transform="rotate(345)"><text transform="translate(0 -145) rotate(90)"><tspan x="0" dy="-4">Help young</tspan><tspan x="0" dy="16">competions</tspan></text></g>
    <g transform="rotate(20)"><text transform="translate(0 -145) rotate(-90)"><tspan x="0" dy="-4">Personalize</tspan><tspan x="0" dy="16">goals for each</tspan></text></g>
    <g transform="rotate(52)"><text transform="translate(0 -150) rotate(-90)"><tspan x="0" dy="-4">Privates</tspan><tspan x="0" dy="16">challenges</tspan></text></g>
    <g transform="rotate(84)"><text transform="translate(0 -145) rotate(-90)" dy="5">Drils spariy</text></g>
    <g transform="rotate(121)"><text transform="translate(0 -150) rotate(-90)"><tspan x="0" dy="-4">Videos past</tspan><tspan x="0" dy="16">fighys</tspan></text></g>
    <g transform="rotate(158)"><text transform="translate(0 -145) rotate(-90)"><tspan x="0" dy="-4">Strong</tspan><tspan x="0" dy="16">condition</tspan></text></g>
    <g transform="rotate(193)"><text transform="translate(0 -140) rotate(90)" dy="5">Nutrition</text></g>
    <g transform="rotate(245)"><text transform="translate(0 -145) rotate(90)" dy="5">Recovery</text></g>
    <g transform="rotate(298)"><text transform="translate(0 -145) rotate(90)"><tspan x="0" dy="-4">Fun trips</tspan><tspan x="0" dy="16">outing</tspan></text></g>
  </g>
  <circle cx="280" cy="280" r="83" fill="#fff"/>
  <text x="280" y="293" text-anchor="middle" font-size="38" fill="var(--green)">OV</text>
  <g fill="#fff" font-size="26">
    <text dominant-baseline="middle"><textPath href="#ring-top" startOffset="21%" text-anchor="middle">Spirit</textPath></text>
    <text dominant-baseline="middle"><textPath href="#ring-top" startOffset="76%" text-anchor="middle">Techincal mind</textPath></text>
    <text dominant-baseline="middle"><textPath href="#ring-bottom" startOffset="50%" text-anchor="middle">Body</textPath></text>
  </g>
</svg>

<p class="abs prep-quote">When the fight was over nothing was solved but nothing<br>mattered we all felt saved</p>

<section class="abs rules"></section>
<div class="abs rules-photo" role="img" aria-label="Portrait photo of a team coach"></div>
<h2 class="abs heading rules-title">I don't want to die without<br>any scars</h2>
<ol class="abs rule-list">
  <li class="rule"><span class="rule-badge"><span class="rule-num">01</span><span class="rule-tag">RULE</span></span><span class="rule-text">Do not talk about OV</span></li>
  <li class="rule"><span class="rule-badge"><span class="rule-num">02</span><span class="rule-tag">RULE</span></span><span class="rule-text">Do nst talk about OV</span></li>
  <li class="rule"><span class="rule-badge"><span class="rule-num">03</span><span class="rule-tag">RULE</span></span><span class="rule-text">You protect the repitation of past present and future OV athetes</span></li>
  <li class="rule"><span class="rule-badge"><span class="rule-num">04</span><span class="rule-tag">RULE</span></span><span class="rule-text">You do not contest close matches or complain</span></li>
  <li class="rule"><span class="rule-badge"><span class="rule-num">05</span><span class="rule-tag">RULE</span></span><span class="rule-text">You will serve as a bridge between kid&nbsp; adult B55 competiting</span></li>
  <li class="rule"><span class="rule-badge"><span class="rule-num">06</span><span class="rule-tag">RULE</span></span><span class="rule-text">You will attend teammate matches and help them whenever possible</span></li>
  <li class="rule"><span class="rule-badge"><span class="rule-num">07</span><span class="rule-tag">RULE</span></span><span class="rule-text">You will alway treat competitiors with respect</span></li>
  <li class="rule"><span class="rule-badge"><span class="rule-num">08</span><span class="rule-tag">RULE</span></span><span class="rule-text">If you are in then you have fo fight</span></li>
</ol>

<footer class="abs footer"></footer>
<div class="abs faq">
  <h2 class="heading faq-title">Common Questions</h2>
  <p class="faq-text">Why the "G2"? This is the second generation of our club. We were founded in the early 2000's. by close of hard rock fans who banned group together to create more unique concert experiences. Many of Order Vantage's guay members are still fritals and some even sponsor some 62 men bes&nbsp; How does someone get invital? pale are accepting indications of interest from competitors born in 2001 &amp; 2008</p>
  <div class="abs btn faq-btn">View More</div>
</div>
<div class="abs brand-foot">Order Vantage</div>
<nav class="abs foot-links"><span>Terms &amp; conditions</span><span>Privacy Policy</span><span>About Us</span><span>Support</span></nav>
<p class="abs copyright">Copyright© 2023 <span class="link">Order Vantage</span> &nbsp;|&nbsp; All Rights Reserved</p>
<div class="abs socials">
  <span class="social is-active" role="img" aria-label="Gatherly"></span>
  <span class="social" role="img" aria-label="Chirpwave"></span>
  <span class="social" role="img" aria-label="Workvine"></span>
  <span class="social" role="img" aria-label="Pixtrelle"></span>
</div>

</body>
</html>
```